i need a business card for a plumbing company in california

we are a drain cleaning , maintenance plumbing company who is starting new marketing campaign for a tatrench-less pipe installation department .

Target Market(s)

the professional who appreciates time and quality workmanship.

Industry/Entity Type

Plumbing

Colors
0655a3
ec1f27

Requirements
Must have
• the second logo needs to be included
Nice to have
• a focus on the services offered
Should not have
• any underlined words on the brief

```html
<!DOCTYPE html>
<html lang="en">
<head>
<meta charset="utf-8">
<title>Clearline Plumbing – Business Card</title>
<link href="https://fonts.googleapis.com/css2?family=Saira:wght@700&family=Arimo:wght@400;700&display=swap" rel="stylesheet">
<style>
  :root {
    --bg: #2b2b2b;
    --card-white: #ffffff;
    --card-grey: #7a776c;
    --brand-red: #e21f26;
    --text-light: #f2f2f2;
    --brand-silver: #e4e4e4;
  }
  * { margin: 0; padding: 0; box-sizing: border-box; }
  html, body { width: 1200px; height: 896px; overflow: hidden; background: var(--bg); }
  .canvas {
    width: 1200px; height: 896px;
    display: flex; flex-direction: column; align-items: center; justify-content: center; gap: 40px;
  }
  .card {
    position: relative; width: 680px; height: 388px; overflow: hidden;
    box-shadow: 0 10px 28px rgba(0,0,0,.45);
  }
  /* Front */
  .card--front { background: var(--card-white); }
  .front__band {
    position: absolute; left: 0; right: 0; top: 178px; bottom: 0; background: var(--card-grey);
  }
  .brand {
    position: absolute; display: flex; align-items: center; gap: 16px;
    font-family: "Saira", sans-serif; font-weight: 700; line-height: .9;
  }
  .brand__mark { width: 26px; height: 26px; background: var(--brand-red); flex: none; }
  .card--front .brand { left: 250px; top: 52px; font-size: 50px; color: var(--card-grey); }
  .person {
    position: absolute; left: 190px; top: 210px; color: var(--text-light);
    font-family: "Arimo", sans-serif;
  }
  .person__name { font-weight: 700; font-size: 19px; letter-spacing: 1px; }
  .person__role { font-size: 16px; margin-top: 3px; }
  .contacts {
    position: absolute; left: 380px; top: 212px; list-style: none;
    font-family: "Arimo", sans-serif; font-size: 17px; color: var(--text-light);
  }
  .contacts li { display: flex; align-items: center; gap: 9px; height: 25px; }
  .contacts svg { width: 13px; height: 13px; fill: var(--text-light); flex: none; }
  /* Back */
  .card--back { background: var(--card-grey); }
  .card--back .brand { left: 200px; top: 110px; font-size: 70px; color: var(--brand-silver); }
  .address {
    position: absolute; left: 120px; top: 300px; font-family: "Arimo", sans-serif;
    font-size: 18px; color: var(--text-light);
  }
</style>
</head>
<body>
<main class="canvas">
  <section class="card card--front" aria-label="Business card front">
    <div class="front__band"></div>
    <div class="brand">
      <div class="brand__name">Clearline<br>Plumbing</div>
      <span class="brand__mark"></span>
    </div>
    <div class="person">
      <div class="person__name">DANIEL REYES</div>
      <div class="person__role">Managing Director</div>
    </div>
    <ul class="contacts">
      <li><svg viewBox="0 0 16 16"><path d="M3 2h3l1.5 3.5-2 1.2a8 8 0 0 0 3.8 3.8l1.2-2L14 10v3a1 1 0 0 1-1 1A11 11 0 0 1 2 3a1 1 0 0 1 1-1z"/></svg>555-014 223 870</li>
      <li><svg viewBox="0 0 16 16"><path d="M4 1h8a1 1 0 0 1 1 1v12a1 1 0 0 1-1 1H4a1 1 0 0 1-1-1V2a1 1 0 0 1 1-1zm1 2v9h6V3z"/></svg>555-014 223 871</li>
      <li><svg viewBox="0 0 16 16"><path d="M1 3h14v10H1zm1.5 1.5v.3L8 9l5.5-4.2v-.3z"/></svg>hello@clearlineplumb.com</li>
      <li><svg viewBox="0 0 16 16"><path d="M8 1a7 7 0 1 0 0 14A7 7 0 0 0 8 1zm0 1.5c.8 1 1.4 2.4 1.6 4H6.4C6.6 4.9 7.2 3.5 8 2.5zM2.6 9.5h2.3c.1 1.5.5 2.9 1.1 3.8a5.6 5.6 0 0 1-3.4-3.8zm0-3h2.3c.1-1.5.5-2.9 1.1-3.8a5.6 5.6 0 0 0-3.4 3.8zm3.8 3h3.2c-.2 1.6-.8 3-1.6 4-.8-1-1.4-2.4-1.6-4zm3.6 3.8c.6-.9 1-2.3 1.1-3.8h2.3a5.6 5.6 0 0 1-3.4 3.8zm1.1-6.8c-.1-1.5-.5-2.9-1.1-3.8a5.6 5.6 0 0 1 3.4 3.8z"/></svg>www.clearlineplumb.com</li>
    </ul>
  </section>

  <section class="card card--back" aria-label="Business card back">
    <div class="brand">
      <div class="brand__name">Clearline<br>Plumbing</div>
      <span class="brand__mark"></span>
    </div>
    <p class="address">4821 Harbor Lane, Oakridge, CA 95012</p>
  </section>
</main>
</body>
</html>
```